Recruitment Web Site Design

I need a Recruitment website explaining who we are and what services we deliver.
This is a new company and the image we portray is extremely important. Must be very professional.
Our target marget are bluechip companies and professionals including executives.

The final design should communicate connecting professionals matching company and individual needs.

Target Market(s)

Corporate, Blue Chip Companies, Professionals/Executives

Industry/Entity Type

It Company

Requirements
Must have
• Must be professional and Sophisticated.
Must have a few tabs.

Must be unique to the norm of websites as I am looking for something different.
Nice to have
• Good graphics with people connecting. Multi - racial pics will be good as we are in South Africa and diversity is a must.
Also a front page (be unique).

I am putting this out there for you to use your imagination and come up with something brilliant.

A few websites you can base ideas from

www.meadowcraftly.com
www.kelpnestor.co.za
www.vuo.co.za
www.lom.co.za

```html
<!DOCTYPE html>
<html lang="en">
<head>
<meta charset="utf-8">
<title>Veranta Recruitment</title>
<link rel="stylesheet" href="https://fonts.googleapis.com/css2?family=Source+Sans+3:wght@400;600&family=Dosis:wght@300;400&display=swap">
<style>
:root{
  --red:#d9000d;
  --red-dark:#b5000a;
  --ink:#333;
  --muted:#555;
  --light:#f2f2f2;
  --line:#dcdcdc;
  --footer:#262626;
  --white:#fff;
}
*{margin:0;padding:0;box-sizing:border-box}
html,body{width:927px;height:1200px;overflow:hidden}
body{position:relative;background:var(--white);font-family:"Source Sans 3",sans-serif;color:var(--ink)}
.abs{position:absolute}
.topbar{left:0;top:0;width:927px;height:4px;background:#2a2a2a}
.brand{left:28px;top:34px;display:flex;align-items:center;gap:12px}
.brand-mark{width:44px;height:44px;background:var(--red);border-radius:50%}
.brand-name{font-family:"Source Sans 3",sans-serif;font-size:25px;letter-spacing:5px;color:#555;line-height:1}
.brand-sub{font-size:8px;letter-spacing:4px;color:#555;margin-top:4px;padding-left:16px}
.call{left:597px;top:18px;font-size:18px;color:#555;font-weight:400}
.call b{font-weight:400;color:#444}
.btn-dark{top:14px;height:25px;background:#1d1d1d;color:#fff;font-size:13px;border-radius:3px;display:flex;align-items:center;justify-content:center}
.signup{left:774px;width:60px}
.login{left:840px;width:54px}
.nav{right:45px;top:80px;display:flex;height:30px;align-items:center}
.nav a{color:var(--red);text-decoration:none;font-size:14px;padding:0 18px;border-right:1px solid var(--line);line-height:32px}
.nav a:last-child{border-right:none;padding-right:0}
.hero-band{left:0;top:120px;width:927px;height:316px;background:linear-gradient(90deg,var(--red),#e8000f 50%,var(--red))}
.hero-card{left:20px;top:109px;width:887px;height:313px;background:var(--white);border-radius:0 0 8px 8px;overflow:hidden}
.hero-title{left:37px;top:64px;font-family:"Dosis",sans-serif;font-weight:400;font-size:28px;line-height:31px;color:#333}
.hero-title span{color:var(--red)}
.hero-sub{left:38px;top:134px;font-size:15px;color:#333}
.hero-text{left:38px;top:153px;width:290px;font-size:11.5px;line-height:18.5px;color:#444}
.btn-red{left:39px;top:218px;width:92px;height:24px;background:var(--red);color:#fff;font-size:13px;border-radius:2px;display:flex;align-items:center;justify-content:center}
.hero-visual{left:370px;top:8px;width:515px;height:303px;background:linear-gradient(180deg,#fff 0%,#f2f2f2 55%,#d7d7d7 100%)}
.features{left:0;top:436px;width:927px;height:157px;background:var(--light);border-bottom:1px solid #e2e2e2}
.feature{top:20px;width:270px}
.feature h3{display:flex;align-items:center;gap:8px;font-size:17px;font-weight:400;color:#333;height:26px}
.feature p{font-size:10px;line-height:18px;color:#555;margin-top:8px}
.btn-black{display:inline-block;background:#111;color:#fff;font-size:10.5px;padding:3px 10px;border-radius:2px;margin-top:10px}
.welcome{left:32px;top:615px;width:580px}
.welcome h2,.howwork h2,.col h2{font-size:16px;font-weight:400;color:#333}
.welcome .lead{font-size:12px;margin-top:8px;color:#333}
.welcome p.body{font-size:10px;line-height:18px;color:#555;margin-top:2px}
.more{display:flex;align-items:center;gap:6px;color:var(--red);font-size:12px}
.more i{display:inline-block;width:12px;height:12px}
.howwork{left:643px;top:615px}
.howwork .media{margin-top:11px;width:249px;height:161px;border:1px solid #ccc;background:radial-gradient(circle at 50% 75%,#e3371f 0%,#f08a70 18%,#e9e9e9 40%,#cfcfcf 100%)}
.col{top:832px;width:196px}
.col .media{margin-top:10px;width:196px;height:82px;border:1px solid #ddd;box-shadow:0 0 2px rgba(0,0,0,.15)}
.col .lead{font-size:12px;line-height:16px;margin-top:14px;color:#333}
.col p.body{font-size:10px;line-height:16.5px;color:#555;margin-top:8px;text-align:justify}
.col .more{margin-top:10px}
.divider{top:860px;height:236px;border-left:1px dotted #bbb}
.footer{left:0;top:1120px;width:927px;height:80px;background:var(--footer);border-top:2px solid #3a3a3a}
.copy{left:32px;top:18px;color:#ddd;font-size:10.5px}
.foot-nav{right:38px;top:14px;color:#ddd;font-size:10.5px}
.foot-nav span{padding:0 5px}
</style>
</head>
<body>
<div class="abs topbar"></div>

<div class="abs brand">
  <span class="brand-mark"></span>
  <div>
    <div class="brand-name">VERANTA</div>
    <div class="brand-sub">RECRUITMENT</div>
  </div>
</div>

<div class="abs call">Call Us: <b>555 210 4478</b></div>
<div class="abs btn-dark signup">Sign up</div>
<div class="abs btn-dark login">Login</div>

<nav class="abs nav">
  <a href="#">Home</a><a href="#">About Us</a><a href="#">Services</a><a href="#">How We Work</a><a href="#">Support</a><a href="#">Blog</a><a href="#">Contact</a>
</nav>

<div class="abs hero-band"></div>
<section class="abs hero-card">
  <h1 class="abs hero-title">Outstanding Rectuitment for<br><span>Out Standing People</span></h1>
  <div class="abs hero-sub">Your Veranta Recruitment tittle line here</div>
  <p class="abs hero-text">Lorem ipsum dolor sit amet, consectetuer adipiscing elit. Nam cursus. Morbi ut mi. Nullam enim leo, egestas id, condimentum at.</p>
  <div class="abs btn-red">learn more</div>
  <div class="abs hero-visual" role="img" aria-label="Silhouettes of business professionals standing in a row on a reflective floor with faint upward arrow icons behind them"></div>
</section>

<section class="abs features">
  <div class="abs feature" style="left:43px">
    <h3><svg width="28" height="28" viewBox="0 0 28 28"><circle cx="14" cy="14" r="12" fill="none" stroke="#111" stroke-width="3"/><path d="M8 14l5 5 9-11" fill="none" stroke="#111" stroke-width="3.5"/></svg>Right Way to find</h3>
    <p>Lorem ipsum dolor sit amet, consectetuer adipiscing elit. Nam cursus. Morbi ut mi. Nullam enim leo, egestas id, condimentum at, laoreet mattis.</p>
    <span class="btn-black">read more</span>
  </div>
  <div class="abs feature" style="left:335px">
    <h3><svg width="26" height="28" viewBox="0 0 26 28"><circle cx="13" cy="8" r="6" fill="#111"/><path d="M1 27c0-8 5-12 12-12s12 4 12 12z" fill="#111"/></svg>Recruitment Candidates</h3>
    <p>Lorem ipsum dolor sit amet, consectetuer adipiscing elit. Nam cursus. Morbi ut mi. Nullam enim leo, egestas id, condimentum at, laoreet mattis.</p>
    <span class="btn-black">read more</span>
  </div>
  <div class="abs feature" style="left:625px">
    <h3><svg width="24" height="28" viewBox="0 0 24 28"><path d="M7 2h3v11h2V9h3v5h2v-3h3v12l-3 4H9l-6-9 2-2 2 2z" fill="#111"/></svg>Send us Your CV</h3>
    <p>Lorem ipsum dolor sit amet, consectetuer adipiscing elit. Nam cursus. Morbi ut mi. Nullam enim leo, egestas id, condimentum at, laoreet mattis.</p>
    <span class="btn-black">read more</span>
  </div>
</section>

<section class="abs welcome">
  <h2>Welcome to Our Website Mainpage</h2>
  <p class="lead">Lorem ipsum dolor sit amet, consectetuer adipiscing elit. Nam cursus.</p>
  <p class="body">Nulla rhoncus dictum metus. Curabitur tristique mi condimentum orci. Phasellus pellentesque aliquam enim. Proin dui lectus, cursus eu, mattis laoreet, viverra sit amet, quam. Curabitur vel dolor ultrices ipsum dictum tristique. Praesent vitae lacus. Ut velit enim, vestibulum non, fermentum nec, hendrerit quis, leo. Pellentesque rutrum malesuada neque.</p>
  <p class="body">Nulla rhoncus dictum metus. Curabitur tristique mi condimentum orci. Phasellus pellentesque aliquam enim. Proin dui lectus, cursus eu, mattis laoreet, viverra sit amet, quam. Curabitur vel dolor ultrices ipsum dictum tristique. Praesent vitae lacus. Ut velit enim, vestibulum non, fermentum nec, hendrerit quis, leo. Pellentesque rutrum malesuada neque.</p>
  <div class="more" style="margin-top:8px;padding-left:8px">read more <i><svg width="12" height="12" viewBox="0 0 12 12"><circle cx="6" cy="6" r="6" fill="#d9000d"/><path d="M5 3.5l3 2.5-3 2.5z" fill="#fff"/></svg></i></div>
</section>

<section class="abs howwork">
  <h2>How we work</h2>
  <div class="media" role="img" aria-label="Video still of a crowd of grey figures with one red figure standing on a red target"></div>
</section>

<section class="abs col" style="left:32px">
  <h2>Who We Are</h2>
  <div class="media" role="img" aria-label="Blue figures with briefcases led by a red figure" style="background:linear-gradient(180deg,#fff,#cfe2f5)"></div>
  <p class="lead">Lorem ipsum dolor sit amet, consect etuer adipiscing elit. Nam cursus.</p>
  <p class="body">Nulla rhoncus dictum metus. Curabitur tristique mi condimentum orci. Phasellus pellentesque aliquam enim. Proin dui lectus, cursus eu, mattis laoreet</p>
  <div class="more">read more <i><svg width="12" height="12" viewBox="0 0 12 12"><circle cx="6" cy="6" r="6" fill="#d9000d"/><path d="M5 3.5l3 2.5-3 2.5z" fill="#fff"/></svg></i></div>
</section>
<div class="abs divider" style="left:236px"></div>

<section class="abs col" style="left:252px">
  <h2>We Provide Services</h2>
  <div class="media" role="img" aria-label="Two people in a job interview across a desk" style="background:linear-gradient(90deg,#6b4a36,#d8d4cc 45%,#f3f3f3)"></div>
  <p class="lead">Lorem ipsum dolor sit amet, consect etuer adipiscing elit. Nam cursus.</p>
  <p class="body">Nulla rhoncus dictum metus. Curabitur tristique mi condimentum orci. Phasellus pellentesque aliquam enim. Proin dui lectus, cursus eu, mattis laoreet</p>
  <div class="more">read more <i><svg width="12" height="12" viewBox="0 0 12 12"><circle cx="6" cy="6" r="6" fill="#d9000d"/><path d="M5 3.5l3 2.5-3 2.5z" fill="#fff"/></svg></i></div>
</section>
<div class="abs divider" style="left:456px"></div>

<section class="abs col" style="left:471px">
  <h2>Consulting &amp; Support</h2>
  <div class="media" role="img" aria-label="Row of linked black paper figures with one red figure in the middle" style="background:linear-gradient(180deg,#f5f5f5,#9a9a9a)"></div>
  <p class="lead">Lorem ipsum dolor sit amet, consect etuer adipiscing elit. Nam cursus.</p>
  <p class="body">Nulla rhoncus dictum metus. Curabitur tristique mi condimentum orci. Phasellus pellentesque aliquam enim. Proin dui lectus, cursus eu, mattis laoreet</p>
  <div class="more">read more <i><svg width="12" height="12" viewBox="0 0 12 12"><circle cx="6" cy="6" r="6" fill="#d9000d"/><path d="M5 3.5l3 2.5-3 2.5z" fill="#fff"/></svg></i></div>
</section>
<div class="abs divider" style="left:676px"></div>

<section class="abs col" style="left:691px">
  <h2>Latest News</h2>
  <div class="media" role="img" aria-label="Diverse team of business professionals standing together" style="background:linear-gradient(180deg,#eef3f4,#a9b4bb 60%,#2b2f38)"></div>
  <p class="lead">Lorem ipsum dolor sit amet, consect etuer adipiscing elit. Nam cursus.</p>
  <p class="body">Nulla rhoncus dictum metus. Curabitur tristique mi condimentum orci. Phasellus pellentesque aliquam enim. Proin dui lectus, cursus eu, mattis laoreet</p>
  <div class="more">read more <i><svg width="12" height="12" viewBox="0 0 12 12"><circle cx="6" cy="6" r="6" fill="#d9000d"/><path d="M5 3.5l3 2.5-3 2.5z" fill="#fff"/></svg></i></div>
</section>

<footer class="abs footer">
  <div class="abs copy">© 2012 Company Name &nbsp;|&nbsp; All right reserved</div>
  <div class="abs foot-nav">Home<span>|</span>About Us<span>|</span>Services<span>|</span>How We Work<span>|</span>Support<span>|</span>Blog<span>|</span>Contact</div>
</footer>
</body>
</html>
```